NZ First of it's kind solutions directory and marketplace for busy Mums needs a business card design

We need a business card design for our new nationwide business in NZ (long term plans to go global). We provide solutions to the everyday challenges that busy Mums face by connecting them with quality communities and suppliers of carefully selected, relevant products and services. We sell direct via our online marketplace. The final design should communicate our values of inclusivity, quality and smart solutions. Colours should incorporate our logo colour palette of #477077 and #6ba8b2. Our website is at https://www.brightnestmums.example

Target Market(s)

busy Mums, Age 28 – 50, female, income over $100K, location main centres NZ primarily but NZ wide. Is likely juggling work or career with a young family. Probably had hobbies which have fallen by the wayside.
-Wants to succeed in her chosen career without compromising on family life
-to successfully juggle her career without feeling like she is compromising her children
- Is time poor, something always has to give and it’s generally her health (she’ll stay up late, get stressed)
- probably ex corporate or professional career. Has discretional income

Industry/Entity Type

Business

Contact Information for Business Card

Lena Forbisher, Founder, BrightNestMums.example (Strapline Tap; Gather; Sorted), 47 Kowhai Terrace, Ellerslie, Auckland 1051, New Zealand. Mob: 021 483 517 Ph: +64 (0)9 571 4860

Font styles to use
Other font styles liked:
• Raleway, and/or Architects Daughter

Colors
00a990
33b8a4
86cfc6
cfeae6

Requirements
Must have
• the above details, streamline. the logo and colours associated with those logos
Should not have
• foil or metallic colours

```html
<!DOCTYPE html>
<html lang="en">
<head>
<meta charset="utf-8">
<title>BrightNestMums – Business Card</title>
<link href="https://fonts.googleapis.com/css2?family=Nunito:wght@800&family=Roboto:ital,wght@0,400;0,500;1,400&display=swap" rel="stylesheet">
<style>
  :root {
    --brand-dark: #3f5f68;
    --brand-mid: #477077;
    --brand-light: #6ba8b2;
    --ink-grey: #3a3f42;
    --card-white: #f7f7f6;
    --page-bg: #e6e6e6;
    --text-on-dark: #ffffff;
  }
  * { box-sizing: border-box; margin: 0; padding: 0; }
  html, body {
    width: 1200px; height: 576px; overflow: hidden;
    background: var(--page-bg);
    font-family: "Roboto", Arial, sans-serif;
  }
  .canvas { position: relative; width: 1200px; height: 576px; }
  .card {
    position: absolute; top: 140px;
    width: 484px; height: 292px;
    background: var(--card-white);
    border-radius: 14px; overflow: hidden;
  }
  .card--front { left: 82px; }
  .card--back { left: 604px; }

  /* Front */
  .front-disc {
    position: absolute; left: 10px; top: 126px;
    width: 176px; height: 176px; border-radius: 50%;
    background: var(--brand-mid);
  }
  .front-brand {
    position: absolute; right: 28px; top: 222px; text-align: right;
  }
  .brand-name {
    font-family: "Roboto", Arial, sans-serif;
    font-weight: 500; color: var(--brand-mid);
    letter-spacing: -0.5px; line-height: 1;
  }
  .front-brand .brand-name { font-size: 32px; }
  .strapline {
    font-size: 10px; letter-spacing: 3.4px; color: var(--ink-grey);
    text-transform: uppercase; white-space: nowrap;
  }
  .strapline .sep { color: var(--brand-light); padding: 0 4px; }
  .front-brand .strapline { margin-top: 8px; margin-right: -3px; }

  /* Back */
  .back-panel { position: absolute; inset: 0; }
  .holder { position: absolute; left: 24px; top: 18px; color: var(--text-on-dark); }
  .holder-name { font-family: "Nunito", Arial, sans-serif; font-weight: 800; font-size: 19px; }
  .holder-role { font-style: italic; font-size: 11.5px; margin-top: 1px; }
  .address {
    position: absolute; left: 24px; top: 156px;
    color: var(--text-on-dark); font-size: 12.5px; line-height: 18.5px;
  }
  .contacts {
    position: absolute; left: 24px; top: 204px; list-style: none;
    color: var(--text-on-dark); font-size: 12px; line-height: 18.5px;
  }
  .contacts li { display: flex; align-items: center; gap: 8px; }
  .contacts svg { width: 11px; height: 11px; fill: var(--text-on-dark); flex: none; }
  .back-brand {
    position: absolute; left: 400px; top: 146px;
    transform: translate(-50%, -50%) rotate(-90deg);
    text-align: right; white-space: nowrap;
  }
  .back-brand .brand-name { font-size: 25px; }
  .back-brand .strapline { font-size: 8.5px; letter-spacing: 3px; margin-top: 8px; }
  .back-dot {
    position: absolute; left: 316px; top: 130px;
    width: 26px; height: 26px; border-radius: 50%;
    background: var(--brand-mid);
  }
</style>
</head>
<body>
<main class="canvas">
  <section class="card card--front" aria-label="Card front">
    <div class="front-disc"></div>
    <div class="front-brand">
      <div class="brand-name">BrightNestMums</div>
      <div class="strapline">Tap<span class="sep">|</span>Gather<span class="sep">|</span>Sorted</div>
    </div>
  </section>

  <section class="card card--back" aria-label="Card back">
    <svg class="back-panel" width="484" height="292" viewBox="0 0 484 292" aria-hidden="true">
      <path d="M0 0 H290 C256 80 250 200 270 292 H0 Z" fill="var(--brand-light)"/>
      <path d="M0 0 H284 C250 80 244 200 264 292 H0 Z" fill="var(--brand-dark)"/>
    </svg>
    <div class="holder">
      <div class="holder-name">Lena Forbisher</div>
      <div class="holder-role">Founder</div>
    </div>
    <address class="address" style="font-style:normal">
      47 Kowhai Terrace, Ellerslie,<br>
      Auckland 1051, New Zealand
    </address>
    <ul class="contacts">
      <li><svg viewBox="0 0 12 12"><rect x="3" y="0.5" width="6" height="11" rx="1.2"/><rect x="4" y="2" width="4" height="6.5" fill="var(--brand-dark)"/></svg>021 483 517</li>
      <li><svg viewBox="0 0 12 12"><path d="M1 4 C1 1.5 11 1.5 11 4 L9 4.5 8.5 3.2 C7 2.8 5 2.8 3.5 3.2 L3 4.5 Z"/><path d="M2.5 6 H9.5 L10.5 11 H1.5 Z"/></svg>+64 (0)9 571 4860</li>
      <li><svg viewBox="0 0 12 12"><path d="M0.5 2.5 H11.5 V9.5 H0.5 Z M1 3 L6 7 L11 3" stroke="var(--brand-dark)" stroke-width="0.8"/></svg>www.BrightNestMums.example</li>
      <li><svg viewBox="0 0 12 12"><circle cx="6" cy="6" r="5.5"/><path d="M0.5 6 H11.5 M6 0.5 C3 3 3 9 6 11.5 M6 0.5 C9 3 9 9 6 11.5" stroke="var(--brand-dark)" stroke-width="0.8" fill="none"/></svg>lena@brightnestmums.example</li>
    </ul>
    <div class="back-dot"></div>
    <div class="back-brand">
      <div class="brand-name">BrightNestMums</div>
      <div class="strapline">Tap<span class="sep">|</span>Gather<span class="sep">|</span>Sorted</div>
    </div>
  </section>
</main>
</body>
</html>
```